Professional looking Roller Blind Discount Card that portrays quality at a value for money price!

We need a double sided business card designed as a discount card. Size 90mm wide x 55mm high.We would like it to look professional and portray quality at a value for money price point.I have uploaded a word document with a basic layout with the information we want included on each side of the card. Please put your own thought into the layout.

Contact Information for Business Card

As per word document attached.

```html
<!DOCTYPE html>
<html lang="en">
<head>
<meta charset="utf-8">
<title>Roller Blinds Discount Card</title>
<link rel="stylesheet" href="https://fonts.googleapis.com/css2?family=Lato:wght@700&family=Open+Sans:wght@400;700&family=Oswald:wght@400&family=Tinos:ital@1&display=swap">
<style>
  :root {
    --brand-blue: #29a8e0;
    --card-white: #ffffff;
    --ink: #2b2b2b;
    --page-bg: #ececec;
    --photo-green: #6f8f55;
    --photo-light: #dfe6e3;
  }
  * { box-sizing: border-box; margin: 0; padding: 0; }
  html, body {
    width: 1200px; height: 900px; overflow: hidden;
    background: var(--page-bg);
    font-family: "Open Sans", Arial, sans-serif;
  }
  .card {
    position: absolute; left: 330px; width: 556px; height: 343px;
    background: var(--card-white);
    box-shadow: 0 2px 6px rgba(0,0,0,0.25);
    overflow: hidden;
  }
  .card--front { top: 90px; }
  .card--back { top: 470px; }

  .band {
    position: absolute; left: 0; width: 100%;
    background: var(--brand-blue); color: var(--card-white);
    display: flex; align-items: center; justify-content: center;
  }
  .band--header { top: 0; height: 61px; }
  .card--back .band--header { height: 57px; }
  .band--footer { bottom: 0; height: 61px; font-size: 20px; }
  .band--footer strong { font-weight: 700; margin: 0 6px; }

  .headline {
    font-family: "Lato", "Open Sans", sans-serif; font-weight: 700;
    font-size: 30px; letter-spacing: 0.3px;
  }
  .card--back .headline { font-size: 28px; }

  .product-lines {
    position: absolute; top: 80px; width: 100%;
    text-align: center; color: var(--ink); font-size: 16px; line-height: 20px;
  }
  .benefits {
    position: absolute; top: 145px; left: 98px;
    display: flex; gap: 31px;
  }
  .benefit {
    width: 100px; height: 100px; border-radius: 50%;
    background: var(--brand-blue); color: var(--card-white);
    display: flex; align-items: center; justify-content: center; text-align: center;
    font-family: "Oswald", "Arial Narrow", sans-serif; font-size: 14px; line-height: 17px;
    letter-spacing: -0.3px; padding: 0 8px;
  }

  .photo {
    position: absolute; top: 57px; left: 0; width: 238px; height: 224px;
    background: linear-gradient(135deg, var(--photo-light) 0%, var(--photo-green) 45%, #4f6a3e 70%, #b9a58c 100%);
  }
  .offer-panel {
    position: absolute; top: 57px; left: 238px; width: 318px; height: 224px;
    background: radial-gradient(circle at 85% 45%, #e6f3fb 0%, var(--card-white) 60%);
    text-align: center; color: var(--ink);
  }
  .offer-panel__quote {
    margin-top: 7px;
    font-family: "Tinos", "Times New Roman", serif; font-style: italic; font-size: 19px;
  }
  .offer-panel__range { margin-top: 14px; font-size: 18px; line-height: 22px; }
  .business-name {
    position: absolute; left: 0; right: 0; top: 170px;
    display: flex; align-items: center; justify-content: center; gap: 10px;
    font-size: 22px; font-weight: 400; color: var(--brand-blue); letter-spacing: 0.5px;
  }
  .business-name__mark { width: 14px; height: 14px; background: var(--brand-blue); }
</style>
</head>
<body>
  <section class="card card--front">
    <header class="band band--header"><h1 class="headline">25% OFF</h1></header>
    <p class="product-lines">Quality Custom Made Roller Blinds<br>Blockout – Screen – Light Filtering</p>
    <ul class="benefits">
      <li class="benefit">“FREE in Home Measure &amp; Quote”</li>
      <li class="benefit">“Best Price Guarantee”</li>
      <li class="benefit">“Family Owned &amp; Operated”</li>
    </ul>
    <footer class="band band--footer">Call <strong>0400 275 913</strong> Today!</footer>
  </section>

  <section class="card card--back">
    <header class="band band--header"><h2 class="headline">ROLLER BLINDS</h2></header>
    <div class="photo" role="img" aria-label="Photo of a sunroom window fitted with a white roller blind, garden greenery outside"></div>
    <div class="offer-panel">
      <p class="offer-panel__quote">FREE in Home Measure &amp; Quote</p>
      <p class="offer-panel__range">Huge Selection<br>Of Fabrics</p>
      <p class="business-name"><span class="business-name__mark"></span>BAYLINE BLINDS</p>
    </div>
    <footer class="band band--footer">Call <strong>0400 275 913</strong> Today</footer>
  </section>
</body>
</html>
```